Psychiatric Office Needs a Website- 1st Time Ever!

Been in practice since 2003 with no website, but finally ready to dive in. We are Maplecrest Behavioral Healthcare, a mental health outpatient practice based in Fayetteville, Georgia that sees diverse individuals and families from childhood to advanced age for a variety of conditions. We've grown by word of mouth and referral but would now like to have a digital footprint. Be the pioneer of our website and we will be sure to share. We would like to see designs that are modern, animated, fairly colorful, easy to read, and caters to all ages. Also, we would like the design to take the whole page (not be centered) and can be viewed well on phone/tablet. Please see our outline for more information. Our motto/slogan is: Maplecrest Behavioral Healthcare- A step forward in your wellness journey, so the design should try to reflect that.
Updates

Project Deadline Extended
Reason: site in progress

Target Market(s)

Children through elderly

Industry/Entity Type

Medical

Logo Text

Stepping forward in your wellness journey

Number of Pages Required

1 page

Colors

Designer to choose colors to be used in the design.

Requirements
Must have
• Animation or moving pictures.
• Color.
• Concise.
• User friendly
• Diversity in the stock photos

```html
<!DOCTYPE html>
<html lang="en">
<head>
<meta charset="utf-8">
<title>Maplecrest Behavioral Healthcare</title>
<link href="https://fonts.googleapis.com/css2?family=Ubuntu:wght@300;400;500;700&display=swap" rel="stylesheet">
<style>
:root{
  --blue:#2a6aa3;
  --blue-dark:#245d90;
  --blue-title:#2f6fa6;
  --green:#6cb33e;
  --green-dark:#5a9a31;
  --text:#555;
  --muted:#888;
  --line:#dcdcdc;
  --footer:#222222;
  --footer-bar:#1a1a1a;
  --news-bg:#efefef;
}
*{margin:0;padding:0;box-sizing:border-box}
html,body{width:1200px;height:2711px;overflow:hidden}
body{font-family:'Ubuntu',sans-serif;color:var(--text);background:#fff;position:relative}
.abs{position:absolute}

/* top bar */
.topbar{position:absolute;left:0;top:0;width:1200px;height:36px;background:var(--blue);color:#fff;font-size:11px;font-weight:500}
.topbar span{position:absolute;top:11px;display:flex;align-items:center;gap:8px}
.topbar svg{width:14px;height:14px}

/* header */
.header{position:absolute;left:0;top:36px;width:1200px;height:141px;background:#fff}
.brand{position:absolute;left:95px;top:20px;display:flex;align-items:center;gap:10px}
.brand-mark{width:22px;height:22px;border-radius:50%;background:var(--green)}
.brand-name{font-size:13px;font-weight:500;color:var(--blue);line-height:1.25;width:130px}
.nav a{position:absolute;top:62px;font-size:12px;font-weight:500;color:#333;text-decoration:none;letter-spacing:.3px}
.nav a.active{color:var(--green)}
.nav a.active::after{content:"";position:absolute;left:0;right:0;bottom:-12px;height:2px;background:var(--green)}
.portal{position:absolute;left:954px;top:49px;width:146px;height:40px;background:var(--green);color:#fff;font-size:14px;font-weight:700;display:flex;align-items:center;justify-content:center;border:2px solid #8ccc63}

/* hero */
.hero{position:absolute;left:0;top:177px;width:1200px;height:528px;background:linear-gradient(90deg,#cfe3f3 0%,#bcd7ee 40%,#d8e8f5 70%,#eef4f9 100%);overflow:hidden}
.hero-photo{position:absolute;left:740px;top:0;width:460px;height:528px;background:linear-gradient(160deg,#f4f7fa 0%,#e1e9f0 60%,#cbd9e6 100%)}
.hero h1{position:absolute;left:97px;top:207px;font-size:35px;font-weight:500;color:var(--blue-title)}
.hero .tag{position:absolute;left:99px;top:256px;font-size:22px;font-weight:500;color:var(--blue-title)}
.btn{position:absolute;background:var(--green);color:#fff;font-weight:700;font-size:15px;display:flex;align-items:center;justify-content:center;gap:10px;letter-spacing:.5px}
.hero .btn{left:100px;top:315px;width:218px;height:45px}
.arrow{position:absolute;width:30px;height:30px}

/* welcome */
.welcome h2{position:absolute;left:100px;top:750px;font-size:27px;font-weight:400;color:var(--blue-title)}
.welcome h2 b{color:var(--green);font-weight:400}
.welcome .lead{position:absolute;left:100px;top:804px;width:600px;font-size:15px;line-height:25px;color:var(--blue-title)}
.welcome .body{position:absolute;left:100px;top:873px;width:600px;font-size:10.5px;line-height:22px;color:#777}
.welcome .btn{left:100px;top:1050px;width:147px;height:44px;font-size:14px}

.appt h3{position:absolute;left:768px;top:744px;width:340px;text-align:center;font-size:23px;font-weight:400;color:var(--blue-title)}
.appt .sub{position:absolute;left:777px;top:779px;width:323px;text-align:center;font-size:11px;color:var(--green)}
.field{position:absolute;left:777px;width:323px;height:38px;border:1px solid var(--line);border-radius:3px;font-size:11px;color:#aaa;padding:12px 10px}
.appt .btn{left:777px;top:1055px;width:323px;height:40px;font-size:15px}

/* services */
.services{position:absolute;left:0;top:1148px;width:1200px;height:491px;background:linear-gradient(180deg,#2b6ba6,#2a67a0)}
.services h2{position:absolute;left:0;top:30px;width:1200px;text-align:center;color:#fff;font-size:27px;font-weight:400}
.services .sub{position:absolute;left:0;top:82px;width:1200px;text-align:center;color:#e6eef6;font-size:14px}
.svc-circle{position:absolute;border-radius:50%;background:#fff;border:6px solid #bcd4ea;display:flex;align-items:center;justify-content:center}
.svc-label{position:absolute;color:#fff;font-size:16px;font-weight:500;text-align:center;width:260px;letter-spacing:.4px}
.svc-nav{position:absolute;top:228px;width:40px;height:40px;border-radius:50%;border:1px solid rgba(255,255,255,.35)}

/* faq */
.faq h2{position:absolute;left:0;top:1679px;width:1200px;text-align:center;font-size:27px;font-weight:400;color:var(--blue-title)}
.q{position:absolute;font-size:14px;color:var(--blue-title);width:460px}
.q::before{content:"";position:absolute;left:-22px;top:5px;width:9px;height:9px;border-radius:50%;border:3px solid var(--green)}
.a{position:absolute;font-size:12px;color:#666;line-height:22px;width:460px}

/* news */
.news{position:absolute;left:0;top:2066px;width:1200px;height:301px;background:var(--news-bg)}
.news h2{position:absolute;left:0;top:30px;width:1200px;text-align:center;font-size:27px;font-weight:400;color:var(--blue-title)}
.news-img{position:absolute;top:126px;width:162px;height:112px}
.news-item{position:absolute;top:128px;width:250px}
.news-item h4{font-size:13px;font-weight:500;color:var(--blue-title);margin-bottom:6px}
.news-item p{font-size:11px;color:#888;line-height:21px}
.news-item a{display:block;font-size:11px;color:var(--green);text-decoration:underline;line-height:20px}
.news-item time{display:block;margin-top:14px;font-size:13px;font-weight:500;color:var(--blue-title)}

/* footer */
.footer{position:absolute;left:0;top:2367px;width:1200px;height:271px;background:var(--footer);color:#bbb}
.footer h5{position:absolute;top:46px;font-size:12px;font-weight:500;color:#fff;letter-spacing:.3px}
.social-name{position:absolute;left:100px;top:84px;font-size:22px;font-weight:700;color:#fff}
.footer .about{position:absolute;left:100px;top:118px;width:260px;font-size:11px;line-height:22px;color:#bbb}
.footer .about em{font-style:normal;color:var(--green)}
.comment{position:absolute;left:428px;width:168px;height:64px;background:#2c2c2c;font-size:11px;line-height:20px;color:#ccc;padding:12px 14px}
.hours{position:absolute;left:683px;top:2454px;font-size:11px;color:#ccc;border-collapse:collapse}
.hours td{height:24px;padding:0}
.hours .day{width:78px;color:var(--green)}
.hours .t{width:56px}
.hours .to{width:40px}
.contact{position:absolute;left:954px;top:2452px;width:160px;font-size:11px;line-height:22px;color:#ccc}
.contact b{font-weight:400;color:var(--green)}
.bottom{position:absolute;left:0;top:2638px;width:1200px;height:73px;background:var(--footer-bar);font-size:11px;color:#aaa}
</style>
</head>
<body>

<div class="topbar">
  <span style="left:100px"><svg viewBox="0 0 16 16" fill="none" stroke="#fff" stroke-width="1.5"><rect x="1.5" y="3" width="13" height="10" rx="1"/><path d="M2 4l6 5 6-5"/></svg>GET A FREE QUOTE NOW!</span>
  <span style="left:640px">LOG IN</span>
  <span style="left:696px">/</span>
  <span style="left:714px"><svg viewBox="0 0 16 16" fill="none" stroke="#fff" stroke-width="1.5"><rect x="4.5" y="1.5" width="7" height="13" rx="1"/></svg>CALL US : (555)014-2290</span>
  <span style="left:878px"><svg viewBox="0 0 16 16" fill="none" stroke="#fff" stroke-width="1.5"><circle cx="8" cy="8" r="6.5"/><path d="M8 4v4l3 2"/></svg>OPENING HOUR MON - SAT  9:00-20:00</span>
</div>

<header class="header">
  <div class="brand">
    <div class="brand-mark"></div>
    <div class="brand-name">Maplecrest Behavioral Healthcare</div>
  </div>
  <nav class="nav">
    <a class="active" style="left:300px">HOME</a>
    <a style="left:370px">ABOUT US</a>
    <a style="left:464px">SERVICES</a>
    <a style="left:553px">CONDITIONS WE TREAT</a>
    <a style="left:725px">NEW PATIENTS</a>
    <a style="left:846px">CONTACT US</a>
  </nav>
  <div class="portal">PATIENT PORTAL</div>
</header>

<section class="hero">
  <div class="hero-photo" role="img" aria-label="Photo of a doctor in a white coat holding a stethoscope"></div>
  <svg class="abs" style="left:700px;top:470px" width="500" height="58" viewBox="0 0 500 58"><path d="M0 58 C120 58 180 20 300 28 C400 34 450 10 500 0 L500 58Z" fill="#fff"/></svg>
  <h1>Maplecrest Behavioral Healthcare</h1>
  <div class="tag">A step forward in your wellness journey</div>
  <div class="btn">TAKE A SCREENING
    <svg width="16" height="16" viewBox="0 0 16 16"><circle cx="8" cy="8" r="8" fill="#fff"/><path d="M6.5 4.5l3.5 3.5-3.5 3.5" stroke="#6cb33e" stroke-width="2" fill="none"/></svg></div>
  <svg class="arrow" style="left:20px;top:250px" viewBox="0 0 30 30"><path d="M20 3L8 15l12 12" stroke="#8a9aa8" stroke-width="4" fill="none"/></svg>
  <svg class="arrow" style="left:1145px;top:250px" viewBox="0 0 30 30"><path d="M10 3l12 12-12 12" stroke="#8a9aa8" stroke-width="4" fill="none"/></svg>
</section>

<section class="welcome">
  <h2>WELCOME TO <b>MBHC</b></h2>
  <p class="lead">Ipsum dolor sit amet, consectetur adipiscing elit, sed do eiusmod tempor dunt ut labore et dolore magna aliqua. Ut enim ad minim veniam, quis nostrud</p>
  <p class="body">Sed ut perspiciatis unde omnis iste natus error sit voluptatem accusantium doloremque laudantium, totam rem aperiam, eaque ipsa quae ab illo inventore veritatis et quasi architecto beatae vitae dicta sunt explicabo. Nemo enim ipsam voluptatem quia voluptas sit aspernatur aut odit aut fugit, sed quia consequuntur magni dolores eos qui ratione voluptatem sequi nesciunt. Neque porro quisquam est, qui dolorem ipsum quia dolor sit amet, consectetur, adipisci velit, sed quia non numquam eius modi tempora incidunt ut labore et dolore magnam aliquam quaerat voluptatem. Ut enim ad minima veniam, quis nostrum exercitationem iusto odio dignissimos ducimus qui blanditiis praesentium voluptatum deleniti atque corrupti quos dolores et quas molestias excepturi sint occaecati cupiditate</p>
  <div class="btn">READ MORE</div>
</section>

<section class="appt">
  <h3>REQUEST FREE APPOINTMENT</h3>
  <div class="sub">Enter your details below and we will contact you.</div>
  <div class="field" style="top:827px">Name</div>
  <div class="field" style="top:882px">E.Mail</div>
  <div class="field" style="top:938px">Phone</div>
  <div class="field" style="top:994px">Type of Treatment
    <svg class="abs" style="right:10px;top:16px" width="8" height="6" viewBox="0 0 8 6"><path d="M0 0h8L4 6z" fill="#aaa"/></svg></div>
  <div class="btn">SUBMIT FORM</div>
</section>

<section class="services">
  <h2>OUR SERVICES</h2>
  <p class="sub">Ipsum dolor sit amet, consectetur adipiscing elit, sed do eiusmod tempor dunt ut labore et dolore magna aliqua</p>
  <svg class="abs" style="left:0;top:0" width="1200" height="491" viewBox="0 0 1200 491" fill="none" stroke="#cfe0f0" stroke-width="2" stroke-dasharray="3 5">
    <path d="M280 266 C320 320 350 335 378 345"/>
    <path d="M420 345 C460 320 480 270 505 245"/>
    <path d="M650 245 C690 290 720 320 745 338"/>
    <path d="M785 338 C820 310 850 270 880 250"/>
  </svg>
  <div class="svc-nav" style="left:26px"><svg width="38" height="38" viewBox="0 0 38 38"><path d="M22 12l-7 7 7 7" stroke="#9fbcd8" stroke-width="2" fill="none"/></svg></div>
  <div class="svc-nav" style="left:1130px"><svg width="38" height="38" viewBox="0 0 38 38"><path d="M16 12l7 7-7 7" stroke="#9fbcd8" stroke-width="2" fill="none"/></svg></div>

  <div class="svc-circle" style="left:150px;top:140px;width:152px;height:152px">
    <svg width="70" height="60" viewBox="0 0 70 60"><path d="M35 58C12 40 2 30 2 18 2 8 10 2 19 2c7 0 12 4 16 9 4-5 9-9 16-9 9 0 17 6 17 16 0 12-10 22-33 40z" fill="#6cb33e"/><path d="M8 30h16l5-9 7 16 5-11 4 4h17" stroke="#fff" stroke-width="3" fill="none"/></svg></div>
  <div class="svc-label" style="left:96px;top:309px">TELEPSYCHIATRY</div>

  <div class="svc-circle" style="left:502px;top:153px;width:152px;height:152px">
    <svg width="50" height="68" viewBox="0 0 50 68"><path d="M25 30C15 20 12 14 12 10 12 4 18 1 25 1s13 3 13 9c0 4-3 10-13 20zM25 30L6 66l-6-6 19-26M25 30l19 36 6-6-19-26" fill="#6cb33e"/><path d="M25 20c-5-5-6-8-6-10 0-3 3-4 6-4s6 1 6 4c0 2-1 5-6 10z" fill="#fff"/></svg></div>
  <div class="svc-label" style="left:448px;top:318px">GROUP THERAPY</div>

  <div class="svc-circle" style="left:867px;top:140px;width:152px;height:152px">
    <svg width="60" height="66" viewBox="0 0 60 66" fill="#6cb33e"><circle cx="18" cy="8" r="7"/><circle cx="42" cy="8" r="7"/><rect x="10" y="18" width="16" height="24" rx="4"/><rect x="34" y="18" width="16" height="24" rx="4"/><rect x="11" y="40" width="6" height="25"/><rect x="19" y="40" width="6" height="25"/><rect x="35" y="40" width="6" height="25"/><rect x="43" y="40" width="6" height="25"/></svg></div>
  <div class="svc-label" style="left:813px;top:309px">FAMILY THERAPY</div>

  <div class="svc-circle" style="left:355px;top:304px;width:82px;height:82px;border-width:5px">
    <svg width="40" height="30" viewBox="0 0 40 30"><path d="M2 4c7-2 13-1 17 3v22c-4-4-10-5-17-3zM38 4c-7-2-13-1-17 3v22c4-4 10-5 17-3z" fill="#6cb33e"/></svg></div>
  <div class="svc-label" style="left:269px;top:409px">PARENTING CLASS</div>

  <div class="svc-circle" style="left:720px;top:301px;width:82px;height:82px;border-width:5px">
    <svg width="40" height="34" viewBox="0 0 40 34" fill="none" stroke="#6cb33e" stroke-width="2.5"><path d="M20 16c-6-5-8-8-8-10 0-3 2-5 4-5s3 1 4 3c1-2 2-3 4-3s4 2 4 5c0 2-2 5-8 10z" fill="#6cb33e"/><path d="M2 26c6-4 10-5 16-3h8c2 0 2 3 0 3h-9M2 32c8-4 20-2 30-8l6-4"/></svg></div>
  <div class="svc-label" style="left:634px;top:405px">MEDICATION CLINICS</div>
</section>

<section class="faq">
  <h2>FAQ</h2>
  <div class="q" style="left:123px;top:1757px">Q. What do I need to bring with me to my first visit?</div>
  <div class="a" style="left:123px;top:1790px">A- Insurance card, patient forms found on our Form's page.</div>
  <div class="q" style="left:123px;top:1842px">Q- What typs of insurance do you accept?</div>
  <div class="a" style="left:123px;top:1874px">A- We accept a large variety of insurance plans. Please click here to view our accepted insurance list.</div>
  <div class="q" style="left:123px;top:1947px">Q- I feel sad, tired and I do not have energy. Is that normal?</div>
  <div class="a" style="left:123px;top:1980px">A- No, If you have these feeling for a long period of time, you may be suffering from depression or other mood disorders.</div>

  <div class="q" style="left:645px;top:1757px">Q- How long do I have to wait to be seen?</div>
  <div class="a" style="left:645px;top:1790px">A- We try to have very little wait time for your convenience.</div>
  <div class="q" style="left:645px;top:1842px">Q- Why is my child not doing well in school?</div>
  <div class="a" style="left:645px;top:1874px">A- Your child may need some testing.</div>
  <div class="q" style="left:645px;top:1947px">Q- I am have trouble with my child. Do you do therapy for children?</div>
  <div class="a" style="left:645px;top:1980px">A- Yes, our psychiatrist is specialized in child, and adolescent psychiatry.</div>
</section>

<section class="news">
  <h2>LATEST NEWS</h2>
  <div class="news-img" style="left:100px;background:linear-gradient(135deg,#e8eef3,#b9c7d3)" role="img" aria-label="Photo of a doctor greeting a patient with a handshake"></div>
  <div class="news-item" style="left:285px">
    <h4>Ipsum dolor sit amet, consectetur</h4>
    <p>Sed ut perspiciatis unde omnis iste natus error sit voluptatem accusantium</p>
    <a>Doloremque laudantium, totam rem</a>
    <time>Sep 20 2017</time>
  </div>
  <div class="news-img" style="left:666px;background:linear-gradient(135deg,#9e8f86,#d9c8bc)" role="img" aria-label="Photo of two people holding hands in comfort"></div>
  <div class="news-item" style="left:853px">
    <h4>Ipsum dolor sit amet, consectetur</h4>
    <p>Sed ut perspiciatis unde omnis iste natus error sit voluptatem accusantium</p>
    <a>Doloremque laudantium, totam rem</a>
    <time>Sep 20 2017</time>
  </div>
</section>

<footer class="footer">
  <h5 style="left:100px">KEEP IN TOUCH</h5>
  <h5 style="left:425px">RECENT COMMENTS</h5>
  <h5 style="left:683px">HOURS</h5>
  <h5 style="left:954px">CONTACT US</h5>
  <div class="social-name">Linkwell</div>
  <p class="about">Lorem ipsum dolor <em>sit amet</em>, <em>consectetur</em> adipiscing elit. Maecenas non magna. Mattis purus sit amet fermentum.<br><br>Maecenas <em>sed diam</em> eget risus varius blandit sit amet non magna.</p>
</footer>
<div class="comment" style="top:2450px">Lorem ipsum dolor sit amet, adipiscing</div>
<div class="comment" style="top:2537px">Lorem ipsum dolor sit amet, adipiscing</div>
<table class="hours">
  <tr><td class="day">Monday</td><td class="t">9:00 am</td><td class="to">to</td><td>4:30 pm</td></tr>
  <tr><td class="day">Tuesday</td><td class="t">9:00 am</td><td class="to">to</td><td>4:30 pm</td></tr>
  <tr><td class="day">Wednesday</td><td class="t">9:00 am</td><td class="to">to</td><td>4:30 pm</td></tr>
  <tr><td class="day">Thursday</td><td class="t">8:30 am</td><td class="to">to</td><td>4:30 pm</td></tr>
  <tr><td class="day">Friday</td><td class="t">9:00 am</td><td class="to">to</td><td>12:00 pm</td></tr>
</table>
<div class="contact">Hours of Operation<br>Closed on major Holidays and weekends After Hours #s,<br>Emergency<br><b>Tel :</b> 555-014-2291</div>

<div class="bottom">
  <span class="abs" style="left:100px;top:30px">Copyright © 2017 MBHC, All Rights Reserved</span>
  <span class="abs" style="left:836px;top:30px">Home &nbsp;/&nbsp; Terms of Use &amp; Privacy Policy &nbsp;/&nbsp; Contact us</span>
</div>

</body>
</html>
```